Medical VIP club - small design

Please read the specs in a design brief attached. Also we don't have logo in a Vector format and attaching the only version we have.

Club

```html
<!DOCTYPE html>
<html lang="en">
<head>
<meta charset="utf-8">
<title>Velmira – Medical VIP Club</title>
<link rel="stylesheet" href="https://fonts.googleapis.com/css2?family=Cinzel+Decorative:wght@700&family=Sorts+Mill+Goudy&family=Questrial&family=PT+Sans:wght@400;700&display=swap">
<style>
:root{
  --page-bg:#d4c197;
  --sheet:#f3ecdc;
  --nav-bg:#dccca6;
  --nav-text:#5e4f36;
  --heading:#7a6b52;
  --body-text:#6e665a;
  --accent:#d8320f;
  --hero-a:#d7381a;
  --hero-b:#ea5d2c;
  --portrait-a:#c9876a;
  --portrait-b:#8a7566;
  --strip:#4b4a45;
  --service:#54482e;
  --sidebar:#e9e0c9;
  --news-red:#c22a10;
  --white:#ffffff;
}
*{margin:0;padding:0;box-sizing:border-box}
html,body{width:1200px;height:1052px;overflow:hidden}
body{background:var(--page-bg);font-family:"PT Sans",Tahoma,sans-serif;position:relative}
.sheet{position:absolute;left:138px;top:0;width:924px;height:969px;background:var(--sheet);box-shadow:0 0 6px rgba(90,70,30,.35)}
.brand{position:absolute;left:28px;top:40px;display:flex;align-items:center;gap:8px;font-family:"Sorts Mill Goudy",serif;font-size:40px;color:var(--accent);line-height:1}
.brand-dot{width:22px;height:22px;border-radius:50%;background:var(--accent)}
.call{position:absolute;left:646px;top:60px;display:flex;align-items:center;gap:8px}
.call-label{font-family:"Sorts Mill Goudy",serif;color:#8c7f6a;line-height:1.15}
.call-label .small{display:block;font-size:18px;margin-left:4px}
.call-label .number{display:block;font-size:26px;letter-spacing:-.3px}
.main-nav{position:absolute;left:0;top:122px;width:924px;height:28px;background:var(--nav-bg);display:flex;align-items:center;font-family:"Sorts Mill Goudy",serif;font-size:12px;text-transform:uppercase;color:var(--nav-text);white-space:nowrap}
.main-nav span{height:100%;display:flex;align-items:center;justify-content:center;border-right:1px solid #efe5cd}
.main-nav span:last-child{border-right:0}
.hero{position:absolute;left:0;top:150px;width:924px;height:402px;background:radial-gradient(ellipse at 40% 45%,var(--hero-b),var(--hero-a) 75%);overflow:hidden}
.hero-title{position:absolute;left:70px;top:86px;font-family:"Cinzel Decorative",serif;font-size:31px;line-height:1.2;color:var(--white);text-shadow:2px 2px 3px rgba(90,20,0,.6);letter-spacing:.5px;white-space:nowrap}
.hero-lines{position:absolute;left:70px;top:138px;font-family:"Questrial",sans-serif;font-size:20px;line-height:20.5px;color:var(--white)}
.register-btn{position:absolute;left:64px;top:283px;width:242px;height:37px;border-radius:19px;background:linear-gradient(#fbf6ec,#d9ccb2);box-shadow:0 2px 3px rgba(80,20,0,.5);font-family:"Questrial",sans-serif;font-size:18px;color:#7a2a14;display:flex;align-items:center;justify-content:center}
.hero-portrait{position:absolute;left:548px;top:0;width:376px;height:402px;background:linear-gradient(180deg,var(--portrait-a),var(--portrait-b))}
.photo-strip{position:absolute;left:0;top:552px;width:924px;height:89px;background:var(--strip)}
.thumb{position:absolute;top:4px;height:81px}
.t1{left:5px;width:181px;background:linear-gradient(90deg,#7a1010,#b52222)}
.t2{left:186px;width:186px;background:linear-gradient(#8b7a55,#d9a24a 55%,#6a5a40)}
.t3{left:372px;width:183px;background:linear-gradient(90deg,#6b5a3c,#c8ad7e)}
.t4{left:555px;width:188px;background:linear-gradient(#ffffff,#e6ebee)}
.t5{left:743px;width:175px;background:linear-gradient(90deg,#ffffff,#e5d6c3)}
.content{position:absolute;left:0;top:641px;width:667px;height:328px}
.section-title{position:absolute;left:26px;font-family:"Sorts Mill Goudy",serif;font-size:20px;line-height:1.2;color:var(--heading);text-transform:uppercase}
.welcome-title{top:12px}
.welcome-text{position:absolute;left:28px;top:44px;width:595px;font-size:11.3px;line-height:18.5px;color:var(--body-text)}
.more{color:var(--accent);font-weight:700;margin-left:12px}
.services-title{top:190px}
.services{position:absolute;left:25px;top:226px;display:flex;gap:13px}
.service-box{width:145px;height:73px;background:var(--service)}
.sidebar{position:absolute;left:669px;top:641px;width:255px;height:328px;background:var(--sidebar);border-left:1px solid #d7cbb0}
.side-title{position:absolute;left:15px;top:12px;font-family:"Sorts Mill Goudy",serif;font-size:20px;line-height:1.2;color:var(--heading)}
.news-item{position:absolute;left:10px;width:235px}
.news-date{font-size:12.5px;font-weight:700;color:var(--news-red);letter-spacing:.3px}
.news-text{font-size:11.3px;line-height:16.5px;color:var(--body-text);margin-top:2px}
.n1{top:48px}
.n2{top:132px}
.divider{position:absolute;left:9px;top:122px;width:232px;border-top:1px dotted #b7a887}
.side-more{position:absolute;right:9px;top:205px;font-size:10.5px;font-weight:700;color:#7a6b52}
.side-more b{color:var(--accent)}
.newsletter{position:absolute;left:0;top:222px;width:255px;height:106px;background:radial-gradient(ellipse at 40% 20%,#e9512a,#a8260e 85%)}
.newsletter-title{position:absolute;left:20px;top:8px;font-family:"Sorts Mill Goudy",serif;font-size:21px;line-height:1.2;color:var(--white)}
.email-field{position:absolute;left:19px;top:43px;width:216px;height:24px;background:#f7f1e3;font-size:10.5px;color:#6e665a;padding:5px 10px}
.subscribe{position:absolute;left:131px;top:76px;width:105px;height:23px;border-radius:12px;background:linear-gradient(#fbf6ec,#d9ccb2);box-shadow:0 1px 2px rgba(60,10,0,.5);font-size:11.5px;font-weight:700;color:var(--news-red);display:flex;align-items:center;justify-content:center;gap:14px}
.footer-nav{position:absolute;left:0;top:985px;width:1200px;display:flex;justify-content:center;font-size:11.5px;color:#5a5040}
.footer-nav span{padding:0 22px}
.footer-nav i{font-style:normal}
.copyright{position:absolute;left:0;top:1017px;width:1200px;text-align:center;font-size:11px;color:#5a5040}
</style>
</head>
<body>
<div class="sheet">
  <header>
    <div class="brand"><span class="brand-dot"></span>Velmira</div>
    <div class="call">
      <svg width="72" height="46" viewBox="0 0 72 46" aria-hidden="true">
        <ellipse cx="36" cy="42" rx="33" ry="4" fill="#cfc4ad"/>
        <path d="M6 14 Q36 0 66 14 L62 22 L50 18 L48 12 Q36 9 24 12 L22 18 L10 22 Z" fill="#1e1e1e"/>
        <path d="M18 24 L54 24 L62 40 L10 40 Z" fill="#262626"/>
        <circle cx="36" cy="31" r="7" fill="#555"/>
        <circle cx="36" cy="31" r="2.5" fill="#bbb"/>
      </svg>
      <div class="call-label"><span class="small">Call Us</span><span class="number">1800-555-0142</span></div>
    </div>
  </header>
  <nav class="main-nav">
    <span style="width:92px">Home</span>
    <span style="width:95px">About Us</span>
    <span style="width:90px">VIP Club</span>
    <span style="width:89px">Services</span>
    <span style="width:177px">Packages and Prices</span>
    <span style="width:130px">Registration</span>
    <span style="width:127px">Testimonials</span>
    <span style="width:124px">Contacts</span>
  </nav>
  <section class="hero">
    <div class="hero-portrait" role="img" aria-label="Photo of a smiling consultant in a grey blazer"></div>
    <h1 class="hero-title">SOME TEXT COMES HERE</h1>
    <p class="hero-lines">Some Text comes here<br>Some Text comes here<br>Some Text comes here</p>
    <div class="register-btn">Click here to Register</div>
  </section>
  <div class="photo-strip">
    <div class="thumb t1" role="img" aria-label="Photo of an emergency sign"></div>
    <div class="thumb t2" role="img" aria-label="Photo of an airliner above clouds at sunset"></div>
    <div class="thumb t3" role="img" aria-label="Photo of a hotel reception desk"></div>
    <div class="thumb t4" role="img" aria-label="Photo of a team of doctors"></div>
    <div class="thumb t5" role="img" aria-label="Photo of a smiling consultant"></div>
  </div>
  <main class="content">
    <h2 class="section-title welcome-title">Welcome to our site</h2>
    <p class="welcome-text">Lorem ipsum dolor sit amet, consectetuer adipiscing elit. Aenean commodo ligula eget dolor. Aenean massa. Cum sociis natoque penatibus et magnis dis parturient montes, nascetur ridiculus mus.Lorem ipsum dolor sit amet, con-sectetuer adipiscing elit. Aenean commodo ligula eget dolor. Aenean massa. Cum sociis natoque penatibus et magnis dis parturient montes, nascetur ridiculus mus.Lorem ipsum dolor sit amet, consectetuer adipiscing elit. Aenean com-modo ligula eget dolor. Aenean massa. Cum sociis natoque penatibus et magnis dis parturient montes, nascetur ridicu-lus mus.Lorem ipsum dolor sit amet, consectetuer adipiscing elit. Aenean commodo ligula eget dolor. Aenean massa. Cum sociis natoque penatibus et magnis dis parturient montes, nascetur ridiculus mus. <span class="more">more ..</span></p>
    <h2 class="section-title services-title">Services</h2>
    <div class="services">
      <div class="service-box"></div><div class="service-box"></div><div class="service-box"></div><div class="service-box"></div>
    </div>
  </main>
  <aside class="sidebar">
    <h2 class="side-title">Latest News</h2>
    <div class="news-item n1"><div class="news-date">Dec 11th</div><p class="news-text">Lorem ipsum dolor sit amet, consectetuer adipiscing elit. Aenean commodo ligula eget dolor. Aenean massa.</p></div>
    <div class="divider"></div>
    <div class="news-item n2"><div class="news-date">Dec 11th</div><p class="news-text">Lorem ipsum dolor sit amet, consectetuer adipiscing elit. Aenean commodo ligula eget dolor. Aenean massa.</p></div>
    <div class="side-more">more <b>..</b></div>
    <div class="newsletter">
      <h3 class="newsletter-title">Newsletter</h3>
      <div class="email-field">Enter your e-mail here:</div>
      <div class="subscribe">Subscribe
        <svg width="8" height="9" viewBox="0 0 8 9" aria-hidden="true"><path d="M0 0 L8 4.5 L0 9 Z" fill="#4aa3d8"/></svg>
      </div>
    </div>
  </aside>
</div>
<nav class="footer-nav">
  <span>Home</span><i>|</i><span>About Us</span><i>|</i><span>VIP Club</span><i>|</i><span>Services</span><i>|</i><span>Packages and Prices</span><i>|</i><span>Registration</span><i>|</i><span>Testimonials</span><i>|</i><span>Contacts</span>
</nav>
<p class="copyright">© Copyright 2009 - 2010. Your Site Name Dot Com. All Rights Reserved</p>
</body>
</html>
```